KPL Construction we build lodges in Botswana

We need a Design Layout only with Categories where we can update each projects photos.... We have a web address and a host - kpl.construction

```html
<!DOCTYPE html>
<html lang="en">
<head>
<meta charset="utf-8">
<title>KPL Construction</title>
<link href="https://fonts.googleapis.com/css2?family=Exo+2:wght@600;700;800&family=Open+Sans:wght@400;600;700&display=swap" rel="stylesheet">
<style>
:root{
  --navy:#1c3264;
  --green:#4f8a1f;
  --green-light:#b9d39a;
  --ink:#1e2430;
  --muted:#8a93a3;
  --line:#e3e6ea;
  --paper:#ffffff;
  --band:#f1f2f4;
}
*{box-sizing:border-box;margin:0;padding:0}
html,body{width:1200px;height:4110px;overflow:hidden;background:var(--paper)}
body{font-family:"Open Sans",Arial,sans-serif;color:var(--ink);position:relative}
.abs{position:absolute}
h1,h2,.brand{font-family:"Exo 2","Arial Black",sans-serif}

.topbar{top:0;left:0;width:1200px;height:38px;background:var(--navy);color:#fff;font-size:12px;display:flex;justify-content:flex-end;align-items:center;padding-right:112px;gap:14px}
.topbar span{display:flex;align-items:center;gap:6px}
.nav{top:38px;left:0;width:1200px;height:82px;background:#fff;display:flex;align-items:center;padding:0 112px;box-shadow:0 1px 4px rgba(0,0,0,.06);z-index:3}
.brand{font-size:25px;font-weight:800;letter-spacing:.5px;color:var(--navy)}
.brand b{color:var(--green)}
.menu{margin-left:auto;display:flex;gap:34px;font-size:13px;color:#333;align-items:center}
.quote{margin-left:32px;background:var(--green);color:#fff;font-size:11px;font-weight:700;padding:13px 14px}

.hero{top:120px;left:0;width:1200px;height:600px}
.hero-photo{position:absolute;inset:0;background:linear-gradient(180deg,#7fa3cc 0%,#b9c9da 30%,#8a5a33 55%,#5b3a22 80%,#4a6d2a 100%)}
.hero-shade{position:absolute;inset:0;background:rgba(20,20,20,.28)}
.hero h1{position:absolute;top:160px;width:100%;text-align:center;color:#fff;font-size:56px;font-weight:700}
.hero p{position:absolute;top:250px;left:340px;width:520px;text-align:center;color:#fff;font-size:17px;line-height:27px}
.hero .btn{position:absolute;top:345px;left:513px;width:175px;height:50px;background:var(--navy);color:#fff;font-size:13px;font-weight:700;display:flex;align-items:center;justify-content:center;gap:8px}
.dots{position:absolute;top:493px;left:550px;display:flex;gap:10px}
.dots i{width:13px;height:13px;border-radius:50%;background:#fff;display:block}
.dots i.gap{margin-left:10px}

.section-title{width:1200px;text-align:center;font-size:33px;font-weight:700;color:var(--ink);letter-spacing:.5px}
.rule{left:380px;width:440px;height:1px;background:var(--line)}
.tabs{top:950px;left:0;width:1200px;display:flex;justify-content:center;gap:4px}
.tabs span{font-size:14px;padding:10px 26px;background:#e9ecf0;color:#333}
.tabs span.on{background:var(--navy);color:#fff}
.shot{background:linear-gradient(160deg,#8fb0d0,#9a6a3e 55%,#4f6f2c)}

.why{top:1556px;left:0;width:1200px;height:564px;background:linear-gradient(180deg,#1d3a66 0%,#2d5a4a 45%,#4e8a2a 100%)}
.why h2{position:absolute;top:90px;width:100%;text-align:center;color:#fff;font-size:33px;font-weight:700}
.feature{position:absolute;top:200px;width:300px;text-align:center;color:#fff}
.feature h3{margin-top:22px;font-size:19px;font-weight:700;letter-spacing:.5px}
.feature p{margin-top:12px;font-size:13px;line-height:26px;color:#e7ecf0}

.news{background:linear-gradient(160deg,#8db0cf,#a8573a 55%,#3d5f38)}
.news-cap{position:absolute;left:32px;bottom:28px;color:#fff}
.news-cap b{display:block;font-size:15px;letter-spacing:.3px}
.news-cap span{font-size:13px;color:#8cc063}

.partners{top:2748px;left:0;width:1200px;height:137px;background:var(--band)}
.badge{position:absolute;top:27px;width:235px;height:83px;background:#fff;border:1px solid #dde0e4;display:flex;align-items:center;justify-content:center}
.badge i{display:block;width:120px;height:28px;background:#c8ccd2;border-radius:4px}

.about{top:2885px;left:0;width:1200px;height:700px;background:linear-gradient(180deg,#ffffff,#eef1ee)}
.about h2{position:absolute;top:140px;left:112px;font-size:33px;font-weight:700}
.about .bar{position:absolute;top:195px;left:114px;width:44px;height:3px;background:var(--green)}
.about p{position:absolute;top:230px;left:112px;width:480px;font-size:13px;line-height:36px;color:var(--muted)}
.about .btn{position:absolute;top:430px;left:114px;width:124px;height:45px;background:var(--navy);color:#fff;font-size:12px;font-weight:700;display:flex;align-items:center;justify-content:center}

.footer{top:3505px;left:0;width:1200px;height:605px}
.foot-title{position:absolute;top:3695px;font-size:17px;font-weight:700;color:#fff}
.field{position:absolute;height:33px;background:#fff;font-size:10px;color:#777;padding:10px 8px}
.submit{position:absolute;top:3918px;left:633px;width:85px;height:28px;border-radius:14px;background:var(--green);color:#fff;font-size:11px;font-weight:700;display:flex;align-items:center;justify-content:center}
.info{position:absolute;left:795px;display:flex;gap:20px;align-items:center;color:#fff;font-size:12px;line-height:20px}
.info .ic{width:38px;height:38px;border-radius:50%;border:1px solid rgba(255,255,255,.7);display:flex;align-items:center;justify-content:center}
.social{position:absolute;top:3912px;left:796px;display:flex;gap:10px}
.social i{width:26px;height:26px;border-radius:50%;display:block}
.copy{position:absolute;top:4055px;width:1200px;text-align:center;color:#e4e8f0;font-size:12px}
</style>
</head>
<body>

<div class="abs topbar">
  <span><svg width="13" height="10" viewBox="0 0 13 10"><rect width="13" height="10" fill="#fff"/><path d="M0 0l6.5 5L13 0" stroke="#1c3264" fill="none"/></svg>Email: info@kplbuild.example</span>
  <span>|</span>
  <span><svg width="11" height="11" viewBox="0 0 24 24"><path fill="#fff" d="M6.6 10.8a15 15 0 006.6 6.6l2.2-2.2c.3-.3.7-.4 1-.2 1.1.4 2.3.6 3.6.6.6 0 1 .4 1 1V20c0 .6-.4 1-1 1A17 17 0 013 4c0-.6.4-1 1-1h3.5c.6 0 1 .4 1 1 0 1.3.2 2.5.6 3.6.1.3 0 .7-.2 1z"/></svg>Telephone: 1 555 010 2040</span>
</div>

<header class="abs nav">
  <div class="brand"><b>KPL</b> CONSTRUCTION</div>
  <nav class="menu"><span>HOME</span><span>ABOUT US</span><span>PROJECTS</span><span>CATEGORIES</span><span>CONTACT</span></nav>
  <div class="quote">REQUEST A QUOTE</div>
</header>

<section class="abs hero">
  <div class="hero-photo" role="img" aria-label="Timber lodge with wooden stairs and lawn under a blue sky"></div>
  <div class="hero-shade"></div>
  <h1>KPL CONSTRUCTION</h1>
  <p>Sed ut perspiciatis unde omnis iste natus error sit voluptatem accusantium doloremque laudantium</p>
  <div class="btn">VIEW PROJECTS <svg width="14" height="14" viewBox="0 0 14 14"><circle cx="7" cy="7" r="7" fill="#fff"/><path d="M5.5 4l3 3-3 3" stroke="#1c3264" stroke-width="1.8" fill="none"/></svg></div>
  <div class="dots"><i></i><i></i><i class="gap"></i><i></i></div>
  <svg class="abs" style="left:0;top:440px" width="1200" height="170" viewBox="0 0 1200 170">
    <path d="M0 110 L600 152 L1200 110" stroke="#4f8a1f" stroke-width="6" fill="none"/>
    <path d="M0 116 L600 160 L1200 116 L1200 170 L0 170Z" fill="#fff"/>
  </svg>
</section>

<h2 class="abs section-title" style="top:830px">OUR PROJECTS</h2>
<div class="abs rule" style="top:905px"></div>
<div class="abs tabs"><span class="on">ALL</span><span>Featured</span><span>Latest</span></div>

<div class="abs shot" style="left:112px;top:1038px;width:238px;height:219px" role="img" aria-label="Two-storey wooden lodge with green trim"></div>
<div class="abs shot" style="left:112px;top:1265px;width:238px;height:175px" role="img" aria-label="Lakeside timber cabin"></div>
<div class="abs shot" style="left:358px;top:1038px;width:238px;height:168px;background:linear-gradient(160deg,#dfe6ea,#5a5048 60%,#3f5a2a)" role="img" aria-label="Modern glass-front chalet"></div>
<div class="abs shot" style="left:358px;top:1214px;width:238px;height:226px;background:linear-gradient(170deg,#9cc0dd,#c34a45 40%,#e8e3d8 70%,#6a8a3a)" role="img" aria-label="Red-roofed pavilion lodge"></div>
<div class="abs shot" style="left:604px;top:1038px;width:238px;height:219px;background:linear-gradient(160deg,#6e8a4a,#6a4a30 55%,#3a5a28)" role="img" aria-label="Log cabin among trees"></div>
<div class="abs shot" style="left:604px;top:1265px;width:238px;height:175px;background:linear-gradient(160deg,#8fa7c0,#9a5a3a 55%,#4a6a30)" role="img" aria-label="Row of timber chalets"></div>
<div class="abs shot" style="left:850px;top:1038px;width:238px;height:168px;background:linear-gradient(160deg,#f0d080,#a86a30 50%,#4a6a2a)" role="img" aria-label="Wooden deck at sunset"></div>
<div class="abs shot" style="left:850px;top:1214px;width:238px;height:226px;background:linear-gradient(170deg,#7aa6d8,#8a5030 50%,#557a30)" role="img" aria-label="Timber house on a grassy hill"></div>

<section class="abs why" role="img" aria-label="Lush green garden backdrop under a blue tint">
  <h2>WHY CHOOSE US</h2>
  <div class="feature" style="left:94px">
    <svg width="160" height="80" viewBox="0 0 160 80"><path d="M2 60 L80 4 L158 60" stroke="#fff" stroke-width="2" fill="none"/><circle cx="80" cy="42" r="7" fill="#fff"/><path d="M66 66 a14 12 0 0 1 28 0z" fill="#fff"/></svg>
    <h3>CLIENT EXPERIENCE</h3>
    <p>Sed ut perspiciatis unde omnis iste natus error sit voluptatem accusantium doloremque laudantium.</p>
  </div>
  <div class="feature" style="left:450px">
    <svg width="160" height="80" viewBox="0 0 160 80"><path d="M2 60 L80 4 L158 60" stroke="#fff" stroke-width="2" fill="none"/><rect x="70" y="34" width="20" height="32" fill="#fff"/><g fill="#4a6a5a"><rect x="74" y="39" width="4" height="4"/><rect x="82" y="39" width="4" height="4"/><rect x="74" y="47" width="4" height="4"/><rect x="82" y="47" width="4" height="4"/><rect x="77" y="56" width="6" height="10"/></g></svg>
    <h3>RESULTS</h3>
    <p>Sed ut perspiciatis unde omnis iste natus error sit voluptatem accusantium doloremque laudantium.</p>
  </div>
  <div class="feature" style="left:806px">
    <svg width="160" height="80" viewBox="0 0 160 80"><path d="M2 60 L80 4 L158 60" stroke="#fff" stroke-width="2" fill="none"/><path d="M68 46h6v20h-6z M76 46l6-12c3 0 4 2 3 6l-1 4h9c2 0 3 2 3 3l-3 15c0 2-2 4-4 4H76z" fill="#fff"/></svg>
    <h3>HIGH QUALITY</h3>
    <p>Sed ut perspiciatis unde omnis iste natus error sit voluptatem accusantium doloremque laudantium.</p>
  </div>
</section>

<h2 class="abs section-title" style="top:2236px">LATEST NEWS</h2>
<article class="abs news" style="left:112px;top:2345px;width:472px;height:280px" role="img" aria-label="Red-roofed lodges with a footbridge over a pond">
  <div class="news-cap"><b>SUNT INCU QUIOFFICIA</b><span>May 2018</span></div>
</article>
<article class="abs news" style="left:616px;top:2345px;width:472px;height:280px;background:linear-gradient(160deg,#9cb8c8,#8a3a22 50%,#4a6a34)" role="img" aria-label="A-frame timber lodge with large windows">
  <div class="news-cap"><b>SUNT INCU QUIOFFICIA</b><span>May 2018</span></div>
</article>

<section class="abs partners">
  <div class="badge" style="left:99px"><i></i></div>
  <div class="badge" style="left:354px"><i></i></div>
  <div class="badge" style="left:609px"><i></i></div>
  <div class="badge" style="left:864px"><i></i></div>
</section>

<section class="abs about">
  <h2>ABOUT US</h2>
  <div class="bar"></div>
  <p>Sed ut perspiciatis unde omnis iste natus error sit voluptatem accusantium doloremque laudantium, totam rem aperiam, eaque ipsa quae ab illo inventore veritatis et quasi architecto beatae vitae dicta sunt explicabo. Nemo enim ipsam voluptatem quia voluptas sit aspernatur aut odit aut fugit, sed quia consequuntur magni dolores eos qui ratione</p>
  <div class="btn">READ MORE</div>
  <div class="abs" style="left:677px;top:130px;width:411px;height:323px;border:1px solid #9aa0a8"></div>
  <div class="abs" style="left:765px;top:340px;width:292px;height:125px;background:var(--green-light)"></div>
  <div class="abs" style="left:627px;top:156px;width:411px;height:329px;background:linear-gradient(160deg,#e8e4dc,#c9b59a 50%,#6a5a4a)" role="img" aria-label="Bright loft living room with white sofa and tall windows"></div>
</section>

<footer class="abs footer">
  <svg class="abs" style="left:0;top:0" width="1200" height="605" viewBox="0 0 1200 605">
    <path d="M0 90 L600 2 L1200 90 L1200 605 L0 605Z" fill="#1c3264"/>
    <path d="M0 86 L600 0 L1200 86" stroke="#4f8a1f" stroke-width="5" fill="none"/>
  </svg>
</footer>

<h3 class="foot-title" style="left:112px">Get In Touch:</h3>
<div class="field" style="top:3740px;left:112px;width:297px">NAME :</div>
<div class="field" style="top:3740px;left:421px;width:297px">PHONE :</div>
<div class="field" style="top:3784px;left:112px;width:606px">EMAIL :</div>
<div class="field" style="top:3827px;left:112px;width:606px;height:72px">MESSAGE :</div>
<div class="submit">SUBMIT</div>

<h3 class="foot-title" style="left:795px">Contact Information</h3>
<div class="info" style="top:3740px"><div class="ic"><svg width="14" height="18" viewBox="0 0 14 18"><path d="M7 0a7 7 0 00-7 7c0 5 7 11 7 11s7-6 7-11a7 7 0 00-7-7z" fill="#fff"/><circle cx="7" cy="7" r="2.5" fill="#1c3264"/></svg></div><div>KPL construction<br>2,23 Acacia Road, Lowridge</div></div>
<div class="info" style="top:3796px"><div class="ic"><svg width="15" height="15" viewBox="0 0 24 24"><path fill="#fff" d="M6.6 10.8a15 15 0 006.6 6.6l2.2-2.2c.3-.3.7-.4 1-.2 1.1.4 2.3.6 3.6.6.6 0 1 .4 1 1V20c0 .6-.4 1-1 1A17 17 0 013 4c0-.6.4-1 1-1h3.5c.6 0 1 .4 1 1 0 1.3.2 2.5.6 3.6.1.3 0 .7-.2 1z"/></svg></div><div>Phone : 1 555 010 2040</div></div>
<div class="info" style="top:3849px"><div class="ic"><svg width="15" height="11" viewBox="0 0 15 11"><rect width="15" height="11" rx="1" fill="#fff"/><path d="M0 0l7.5 6L15 0" stroke="#1c3264" fill="none"/></svg></div><div>info@kplbuild.example</div></div>
<div class="social"><i style="background:#1c3264;border:1px solid #fff"></i><i style="background:#2a8fd6"></i><i style="background:#d8322a"></i><i style="background:#c9893a"></i></div>

<div class="abs" style="top:4020px;left:112px;width:976px;height:1px;background:rgba(255,255,255,.25)"></div>
<div class="copy">Copyrights © 2019, KPL construction. All Rights Reserved.</div>

</body>
</html>
```